TLK Electricial Contracting Services

Hi guys, after a design for my small electrical company, have logo design files to be incorporated into the layout, the basic concept is electrical contracting services for residential, commercial, industrial & data services, image is clean clear and strong,

Card format is to have a nice clean logo on front,with maybe the Residential – commercial – industrial - data, followed with licensed & insured, followed by contact details on backside of the card.

Target Market(s)

Residential, commercial, industrial sectors.

Industry/Entity Type

Electrical

Contact Information for Business Card

TLK logo,
Residential – commercial – industrial - data
REC: 61307
Email: tlk@vornamail.net.au
Phone: 0487 352 019

Requirements
Must have
• Clean & strong design.
Nice to have
• If possible, I would like the logo colours inverted so the text is orange and the background is black on the front of the card, then the backside of the card be the reverse colour
Should not have
• No Sparks, lightning bolts,

```html
<!DOCTYPE html>
<html lang="en">
<head>
<meta charset="utf-8">
<title>TLK Electricial Contracting Services – Business Card</title>
<link rel="stylesheet" href="https://fonts.googleapis.com/css2?family=Open+Sans:wght@400;600;700;800&display=swap">
<style>
  :root {
    --orange: #e8792a;
    --black: #111111;
    --white: #ffffff;
    --ink: #222222;
    --backdrop: #ecebe8;
  }
  * { margin: 0; padding: 0; box-sizing: border-box; }
  html, body { width: 1200px; height: 1200px; overflow: hidden; }
  body {
    background: var(--backdrop);
    font-family: "Open Sans", Arial, sans-serif;
    position: relative;
  }
  .card {
    position: absolute;
    width: 700px;
    height: 400px;
    overflow: hidden;
    box-shadow: 0 6px 18px rgba(0,0,0,0.18);
  }

  /* Front */
  .card-front {
    left: 420px;
    top: 170px;
    background: var(--orange);
    display: flex;
    align-items: center;
    justify-content: center;
  }
  .brand { text-align: center; font-weight: 800; }
  .brand-mark { font-size: 120px; line-height: 1; letter-spacing: 2px; }
  .brand-name { font-size: 22px; margin-top: 8px; letter-spacing: 0.5px; white-space: nowrap; }
  .card-front .brand { color: var(--white); }
  .sectors {
    margin-top: 18px;
    font-size: 16px;
    font-weight: 600;
    color: var(--white);
    letter-spacing: 0.5px;
    white-space: nowrap;
  }
  .licence {
    margin-top: 6px;
    font-size: 14px;
    font-weight: 700;
    color: var(--black);
    text-transform: uppercase;
    letter-spacing: 2px;
  }

  /* Back */
  .card-back {
    left: 80px;
    top: 520px;
    background: var(--white);
  }
  .holder {
    position: absolute;
    left: 0;
    top: 28px;
    display: flex;
    align-items: flex-start;
  }
  .holder-tab { width: 70px; height: 46px; display: block; }
  .holder-text { margin-left: 12px; }
  .holder-name { color: var(--orange); font-weight: 700; font-size: 26px; line-height: 1.1; }
  .holder-role { color: var(--ink); font-size: 17px; }
  .contact {
    position: absolute;
    left: 52px;
    top: 170px;
    font-size: 16px;
    line-height: 1.35;
    color: var(--ink);
    white-space: nowrap;
  }
  .contact .address { margin-bottom: 14px; }
  .contact .label { color: var(--orange); font-weight: 600; }
  .card-back .brand {
    position: absolute;
    right: 50px;
    top: 140px;
    color: var(--black);
  }
  .card-back .brand-mark { font-size: 96px; }
  .card-back .brand-name { font-size: 15px; }
  .bands {
    position: absolute;
    left: 0;
    bottom: 0;
    width: 700px;
    height: 90px;
    display: block;
  }
</style>
</head>
<body>

  <section class="card card-front" aria-label="Card front">
    <div class="brand">
      <div class="brand-mark">TLK</div>
      <div class="brand-name">TLK Electricial Contracting Services</div>
      <div class="sectors">Residential – Commercial – Industrial – Data</div>
      <div class="licence">Licensed &amp; Insured</div>
    </div>
  </section>

  <section class="card card-back" aria-label="Card back">
    <div class="holder">
      <svg class="holder-tab" viewBox="0 0 70 46" aria-hidden="true">
        <polygon points="0,0 70,0 52,46 0,46" fill="var(--orange)"/>
        <polygon points="36,0 70,0 52,46 18,46" fill="var(--black)"/>
      </svg>
      <div class="holder-text">
        <div class="holder-name">Daniel Hart</div>
        <div class="holder-role">Managing Director</div>
      </div>
    </div>

    <div class="contact">
      <div class="address">12345, Address Goes Here<br>Country Name, 123456</div>
      <div><span class="label">p:</span> 0487 352 019</div>
      <div><span class="label">e:</span> tlk@vornamail.net.au</div>
      <div><span class="label">REC:</span> 61307</div>
    </div>

    <div class="brand">
      <div class="brand-mark">TLK</div>
      <div class="brand-name">TLK Electricial Contracting Services</div>
    </div>

    <svg class="bands" viewBox="0 0 700 90" aria-hidden="true">
      <polygon points="0,20 290,20 278,32 0,32" fill="var(--orange)"/>
      <polygon points="300,20 700,20 700,90 240,90" fill="var(--black)"/>
    </svg>
  </section>

</body>
</html>
```